female esthetician looking for an impact business card

I an an expert in skin care industry with high experience in NYC.I want my business card to look professional , an impact at first look. I do want a combination between white and gold . I believe the font will be great if is gold.. The Fonts are also important. MIRABELA COSTINA (SKIN CARE BOUTIQUE)

THIS SHOULD BE THE BUSINESS NAME, and should be placed on th eback of the card.
IN front m, the name MIRABELA COSTINA - ESTHETCIAN

BY APPOINTMENTS ONLY: 518.240.7136

Target Market(s)

HIGH END CLIENTELE

Contact Information for Business Card

iT WILL BE on a luxury paper. I neeed the wow feeling

Requirements
Should not have
• pictures

```html
<!DOCTYPE html>
<html lang="en">
<head>
<meta charset="utf-8">
<title>Mirabela Costina – Business Card</title>
<link href="https://fonts.googleapis.com/css2?family=Josefin+Sans:wght@300;400&family=Lato:wght@400;700&display=swap" rel="stylesheet">
<style>
  :root {
    --backdrop: #dcdcdc;
    --card: #262626;
    --gold: #e8b923;
    --gold-muted: #b89a3e;
    --white: #f2f2f2;
  }
  html, body {
    margin: 0;
    padding: 0;
    width: 1200px;
    height: 900px;
    overflow: hidden;
    background: var(--backdrop);
  }
  .canvas {
    position: relative;
    width: 1200px;
    height: 900px;
  }
  .card {
    position: absolute;
    width: 560px;
    height: 320px;
    border-radius: 28px;
    background: var(--card);
    box-shadow: 0 10px 28px rgba(0, 0, 0, 0.25);
    overflow: hidden;
  }
  .card--front { left: 100px; top: 120px; }
  .card--back  { left: 540px; top: 470px; }

  .brand {
    display: flex;
    flex-direction: column;
    align-items: center;
  }
  .brand__mark {
    width: 44px;
    height: 44px;
    border-radius: 50%;
    background: var(--gold);
    margin-bottom: 22px;
  }
  .brand__name {
    font-family: "Josefin Sans", sans-serif;
    font-weight: 300;
    color: var(--gold);
    letter-spacing: 2px;
    margin: 0;
    line-height: 1;
  }
  .brand__tagline {
    font-family: "Josefin Sans", sans-serif;
    font-weight: 300;
    color: var(--gold-muted);
    letter-spacing: 8px;
    margin: 6px 0 0;
    line-height: 1;
  }
  .card--front .brand {
    position: absolute;
    left: 0; right: 0; top: 92px;
  }
  .card--front .brand__name { font-size: 36px; }
  .card--front .brand__tagline { font-size: 13px; }

  .card--back .brand {
    position: absolute;
    left: 48px; top: 48px;
    align-items: center;
  }
  .card--back .brand__name { font-size: 30px; }
  .card--back .brand__tagline { font-size: 11px; letter-spacing: 7px; }

  .contact-person {
    position: absolute;
    left: 48px; top: 150px;
    font-family: "Lato", sans-serif;
  }
  .contact-person__name {
    color: var(--gold);
    font-weight: 700;
    font-size: 22px;
    margin: 0;
    letter-spacing: 0.5px;
  }
  .contact-person__role {
    color: var(--white);
    font-size: 16px;
    margin: 2px 0 14px;
  }
  .contact-list {
    list-style: none;
    margin: 0;
    padding: 0;
  }
  .contact-list li {
    display: flex;
    align-items: center;
    gap: 8px;
    color: var(--white);
    font-size: 16px;
    line-height: 24px;
  }
  .contact-list svg { width: 13px; height: 13px; fill: var(--gold); flex: none; }

  .address {
    position: absolute;
    right: 40px; top: 190px;
    font-family: "Lato", sans-serif;
    color: var(--white);
    font-size: 15px;
    line-height: 21px;
    text-align: right;
    margin: 0;
  }
</style>
</head>
<body>
<main class="canvas">

  <section class="card card--front" aria-label="Card front">
    <div class="brand">
      <span class="brand__mark"></span>
      <h1 class="brand__name">MIRABELA COSTINA</h1>
      <p class="brand__tagline">SKIN CARE EXPERT</p>
    </div>
  </section>

  <section class="card card--back" aria-label="Card back">
    <div class="brand">
      <h2 class="brand__name">MIRABELA COSTINA</h2>
      <p class="brand__tagline">SKIN CARE EXPERT</p>
    </div>

    <div class="contact-person">
      <p class="contact-person__name">DANIEL MOREAU</p>
      <p class="contact-person__role">Managing Director</p>
      <ul class="contact-list">
        <li>
          <svg viewBox="0 0 16 16" aria-hidden="true"><path d="M3 1h3l1.5 4-2 1.3a9 9 0 0 0 4.2 4.2L11 8.5l4 1.5v3a2 2 0 0 1-2 2A12 12 0 0 1 1 3a2 2 0 0 1 2-2z"/></svg>
          044-123 456 789
        </li>
        <li>
          <svg viewBox="0 0 16 16" aria-hidden="true"><path d="M1 3h14v10H1z M2 4l6 5 6-5" stroke="#262626" stroke-width="1.2"/></svg>
          info@webname.com
        </li>
        <li>
          <svg viewBox="0 0 16 16" aria-hidden="true"><circle cx="8" cy="8" r="7"/><path d="M1 8h14M8 1c-3 3.5-3 10.5 0 14M8 1c3 3.5 3 10.5 0 14" stroke="#262626" stroke-width="1" fill="none"/></svg>
          www.websitename.com
        </li>
      </ul>
    </div>

    <p class="address">421, Address line here<br>Country Name, 45452</p>
  </section>

</main>
</body>
</html>
```